CANNABIS BASED BUSINESS CARD DESIGN AND CREATION

WE ARE A PRIVATELY OWNED INVESTMENT CORPORATION. WE PRIMARILY INVEST IN LEGAL PUBLICALLY TRADED CANNABIS COMPANIES THAT ARE TRADED THROUGH THE OTC OR VOLTRIX. WE OFFER THE PUBLIC AN OPPORTUNITY TO PARTICIPATE DIRECTLY WITH THESE COMPANIES FOR NO FEES, NO COMMISSIONS AND IN DEPTH RESEARCH ON EVERY COMPANY PROFILE. WE ARE ALSO PRO FEDERAL LEGALIZATION AND WILL APPLY FOR CULTIVATION AND DISPENSARY LICENSES WHEN THEY BECOME AVAILABLE.

Target Market(s)

30-60 FEMALE AND MALE INVESTORS

Industry/Entity Type

Business

Contact Information for Business Card

EDS CAPITAL GROUP CORPERIN D SLAUGHTER(469) 426-6302ERIN@EDSCAPITALGROUP.COM

Font styles to use
Decorative

Requirements
Must have
• COMPANY LOGO
• CANNABIS LOGO
Nice to have
• MODERN FONT AND LOGOS

```html
<!DOCTYPE html>
<html lang="en">
<head>
<meta charset="utf-8">
<title>Orlin Ridge Holdings – Business Card</title>
<link rel="stylesheet" href="https://fonts.googleapis.com/css2?family=Lato:wght@400;700&display=swap">
<style>
  :root {
    --stage: #6b7a12;
    --card-top: #1c1c1c;
    --card-bottom: #050505;
    --brand-green: #2fb24f;
    --text-light: #f2f2f2;
    --text-muted: #9a9a9a;
    --rule: #2e2e2e;
    --leaf-shade: rgba(255, 255, 255, 0.05);
  }
  * { margin: 0; padding: 0; box-sizing: border-box; }
  html, body {
    width: 1200px; height: 900px; overflow: hidden;
    background: var(--stage);
    font-family: "Lato", Arial, sans-serif;
  }
  .canvas { position: relative; width: 1200px; height: 900px; }
  .card {
    position: absolute;
    width: 580px; height: 330px;
    border-radius: 20px;
    background: linear-gradient(160deg, var(--card-top) 0%, var(--card-bottom) 70%);
    overflow: hidden;
  }
  .card--front { left: 70px; top: 80px; }
  .card--back { left: 550px; top: 490px; }

  .brand-name {
    color: var(--brand-green);
    font-weight: 400;
    letter-spacing: 1px;
    white-space: nowrap;
  }
  .brand-mark {
    display: inline-block;
    background: var(--brand-green);
    border-radius: 50%;
    vertical-align: middle;
  }

  /* front */
  .front-decor {
    position: absolute;
    right: 30px; top: 20px;
    width: 230px; height: 290px;
    border-radius: 45% 45% 40% 40%;
    background: radial-gradient(ellipse at center, var(--leaf-shade) 0%, rgba(255,255,255,0) 70%);
  }
  .front-brand {
    position: absolute;
    left: 0; right: 0; top: 140px;
    text-align: center;
  }
  .front-brand .brand-mark { width: 18px; height: 18px; margin-right: 12px; }
  .front-brand .brand-name { font-size: 30px; vertical-align: middle; }

  /* back */
  .back-brand {
    position: absolute;
    right: 40px; top: 62px;
  }
  .back-brand .brand-mark { width: 12px; height: 12px; margin-right: 8px; }
  .back-brand .brand-name { font-size: 19px; vertical-align: middle; }
  .back-rule {
    position: absolute;
    left: 40px; right: 40px; top: 140px;
    height: 1px; background: var(--rule);
  }
  .holder-name {
    position: absolute;
    left: 40px; top: 190px;
    color: var(--text-light);
    font-size: 19px; font-weight: 400;
    letter-spacing: 0.5px;
    padding-bottom: 10px;
    border-bottom: 1px solid var(--rule);
    width: 230px;
  }
  .contact-list {
    position: absolute;
    right: 40px; top: 170px;
    list-style: none;
  }
  .contact-item {
    display: flex; align-items: center;
    color: var(--text-muted);
    font-size: 13px;
    margin-bottom: 9px;
  }
  .contact-icon { width: 14px; height: 14px; margin-right: 12px; fill: var(--brand-green); }
</style>
</head>
<body>
<main class="canvas">

  <section class="card card--front" aria-label="Card front">
    <div class="front-decor" role="img" aria-label="Faint cannabis leaf decoration"></div>
    <div class="front-brand">
      <span class="brand-mark"></span><span class="brand-name">Orlin Ridge Holdings</span>
    </div>
  </section>

  <section class="card card--back" aria-label="Card back">
    <div class="back-brand">
      <span class="brand-mark"></span><span class="brand-name">Orlin Ridge Holdings</span>
    </div>
    <div class="back-rule"></div>
    <p class="holder-name">MARLA J PENDLEBURY</p>
    <ul class="contact-list">
      <li class="contact-item">
        <svg class="contact-icon" viewBox="0 0 16 16" aria-hidden="true"><path d="M3 2h3l1.5 3.5-2 1.3a8 8 0 0 0 3.7 3.7l1.3-2L14 10v3a1 1 0 0 1-1 1A11 11 0 0 1 2 3a1 1 0 0 1 1-1z"/></svg>
        (555) 013-4478
      </li>
      <li class="contact-item">
        <svg class="contact-icon" viewBox="0 0 16 16" aria-hidden="true"><path d="M1 3h14v10H1z M1 3l7 5 7-5" fill="var(--brand-green)" stroke="#0b0b0b" stroke-width="1.2"/></svg>
        marla@tqmcapitalgroup-demo.com
      </li>
      <li class="contact-item">
        <svg class="contact-icon" viewBox="0 0 16 16" aria-hidden="true"><path d="M6.5 9.5l3-3M7 4.5l1.5-1.5a2.8 2.8 0 0 1 4 4L11 8.5M9 11.5L7.5 13a2.8 2.8 0 0 1-4-4L5 7.5" fill="none" stroke="var(--brand-green)" stroke-width="1.8" stroke-linecap="round"/></svg>
        www.orlinridge-demo.com
      </li>
    </ul>
  </section>

</main>
</body>
</html>
```